Health Clinic treating people with mental illness needs a website

We need a website for a new mental health clinic based in Florida called Solvane Wellness USA. We treat people with mental health issues such as depression, PTSD, Bipolar, chronic pain, etc. I want the website to be easy to follow and inviting to the visitors. It should be easy to locate the different treatment options and how to go about contacting and making appointments. The images on the website should be something that the patients can relate to, whether a close up of a woman's face, something that conveys emotion. The patients visiting this website are often sad and miserable, they need to be able to feel comfortable when they look at this website. I want them to feel that we understand where they are coming from. I like colors such as purple, turquoise, lavender.

Target Market(s)

College students, veterans, anyone with mental illness

Industry/Entity Type

Health And Wellness

Font styles to use
Serif
Sans Serif

Colors

Designer to choose colors to be used in the design.

Requirements
Must have
• There should be a home/landing page, about us page, treatment page, contact page, and a FAQ page. I've included my logo below.
Nice to have
• The flow of the web pages should be calming and welcoming. I want people to feel warm and understood when they enter our page.
Should not have
• The images and writing should not be overly stimulating or aggressive.

```html
<!DOCTYPE html>
<html lang="en">
<head>
<meta charset="utf-8">
<title>Solvane Wellness USA</title>
<link href="https://fonts.googleapis.com/css2?family=Montserrat:wght@400;500;600&family=Roboto+Condensed:wght@400;500&display=swap" rel="stylesheet">
<style>
:root{
  --purple:#b565ab;
  --purple-dark:#9c4b92;
  --lavender:#c88fc0;
  --lavender-soft:#f0deed;
  --teal:#30b5a2;
  --teal-dark:#279a8a;
  --mint:#86d1c6;
  --mint-dark:#6cb9ae;
  --grey-bg:#f4f4f4;
  --footer:#2a2a2a;
  --text:#333;
  --white:#fff;
}
*{margin:0;padding:0;box-sizing:border-box}
html,body{width:1200px;height:2522px;overflow:hidden}
body{position:relative;font-family:"Montserrat",sans-serif;color:var(--text);background:var(--white)}
.abs{position:absolute}
.cond{font-family:"Roboto Condensed",sans-serif}

.topbar{left:0;top:0;width:1200px;height:31px;background:var(--purple);color:var(--white);font-size:13px;font-weight:500}
.topbar .addr{left:112px;top:8px;display:flex;align-items:center;gap:6px}
.topbar .tel{right:112px;top:8px;display:flex;align-items:center;gap:6px}

.header{left:0;top:31px;width:1200px;height:124px;background:var(--white)}
.brand{display:flex;align-items:center;gap:10px;color:#5a2a6e;font-family:"Montserrat",sans-serif;font-weight:600}
.header .brand{left:112px;top:44px;font-size:24px}
.brand .dot{width:22px;height:22px;border-radius:50%;background:var(--purple);flex:none}
.nav{right:112px;top:54px;display:flex;gap:0;align-items:center;font-size:15px}
.nav a{color:var(--text);text-decoration:none;padding:11px 12px;margin-left:14px}
.nav a.active{background:var(--lavender-soft);color:var(--purple);font-weight:600;margin-left:0}

.hero{left:0;top:155px;width:1200px;height:639px;background:linear-gradient(100deg,#8d6c55 0%,#b99c80 25%,#c9b39a 50%,#b8a28a 70%,#6e5648 100%)}
.hero .brand{right:112px;top:270px;color:var(--white);font-size:44px;font-weight:500}
.hero .brand .dot{width:40px;height:40px;background:var(--white)}
.card{top:576px;width:318px;height:201px;padding:14px 26px;color:var(--white)}
.card h3{font-family:"Roboto Condensed",sans-serif;font-weight:500;font-size:25px;margin-bottom:14px}
.card p{font-size:15px;line-height:24px;text-align:justify;font-weight:400}
.card .btn{position:absolute;left:27px;top:148px;padding:9px 13px;font-size:14px;font-weight:500;color:var(--white)}
.card.c1{left:112px;background:rgba(200,143,192,.92)}
.card.c1 .btn{background:var(--purple-dark)}
.card.c2{left:441px;background:rgba(48,181,162,.95)}
.card.c2 .btn{background:var(--teal-dark)}
.card.c3{left:770px;background:rgba(134,209,198,.92)}
.card.c3 .btn{background:var(--mint-dark)}

.schedule{left:0;top:794px;width:1200px;height:82px;background:var(--purple)}
.schedule h2{left:112px;top:25px;color:var(--white);font-family:"Roboto Condensed",sans-serif;font-weight:500;font-size:28px}
.schedule .book{left:823px;top:18px;width:265px;height:47px;background:var(--purple-dark);color:var(--white);border-radius:3px;font-family:"Roboto Condensed",sans-serif;font-weight:500;font-size:17px;display:flex;align-items:center;justify-content:center}

.sec-title{left:0;width:1200px;text-align:center;color:var(--purple);font-family:"Roboto Condensed",sans-serif;font-weight:500;font-size:36px}
.feature{top:1031px;width:280px;text-align:center}
.feature .icon{width:106px;height:106px;border-radius:50%;background:var(--purple);margin:0 auto 14px;display:flex;align-items:center;justify-content:center}
.feature .icon span{width:40px;height:46px;border-radius:20px 20px 6px 6px;background:rgba(255,255,255,.9)}
.feature h3{color:var(--purple);font-family:"Roboto Condensed",sans-serif;font-weight:500;font-size:24px;margin-bottom:8px}
.feature p{font-size:14px;line-height:23px;color:#333}
.feature .more{display:block;margin-top:14px;color:var(--purple);font-family:"Roboto Condensed",sans-serif;font-size:19px;font-weight:500}

.options{left:0;top:1388px;width:1200px;height:559px;background:var(--grey-bg)}
.tile{top:156px;width:244px;height:325px}
.tile.photo1{left:112px;background:linear-gradient(120deg,#c9a88a,#8a6a55 45%,#e0c64a 75%,#5a7fb5)}
.tile.photo2{left:600px;background:linear-gradient(120deg,#b9aba0,#e8d6d0 45%,#a58a7a 75%,#6e6055)}
.tile.text{padding:44px 22px;text-align:center;color:var(--white)}
.tile.text h3{font-family:"Roboto Condensed",sans-serif;font-weight:500;font-size:24px;margin-bottom:18px}
.tile.text p{font-size:13.5px;line-height:22.5px}
.tile.text .btn{display:inline-block;margin-top:26px;padding:10px 13px;font-size:14px;font-weight:500}
.tile.t1{left:356px;background:var(--teal)}
.tile.t1 .btn{background:var(--teal-dark)}
.tile.t2{left:844px;background:var(--mint)}
.tile.t2 .btn{background:var(--mint-dark)}

.news-p{left:0;top:2077px;width:1200px;text-align:center;font-size:15px;color:#444}
.email{left:113px;top:2152px;width:974px;height:48px;border:2px solid #ddd;padding:14px 11px;font-size:15px;color:#444}
.subscribe{left:113px;top:2212px;width:974px;height:48px;background:var(--purple);color:var(--white);font-family:"Roboto Condensed",sans-serif;font-weight:500;font-size:17px;display:flex;align-items:center;justify-content:center}

.footer{left:0;top:2351px;width:1200px;height:171px;background:var(--footer);color:var(--white)}
.footer .brand{left:112px;top:72px;color:var(--white);font-size:28px;font-weight:500}
.footer .brand .dot{width:30px;height:30px;background:var(--white)}
.social{top:35px;width:42px;height:42px;border:2px solid var(--white);border-radius:50%}
.footer .rule{left:622px;top:95px;width:466px;height:1px;background:#aaa}
.footer .copy{right:112px;top:128px;font-size:15px;font-weight:500}
</style>
</head>
<body>

<div class="abs topbar">
  <div class="abs addr">
    <svg width="10" height="14" viewBox="0 0 10 14"><path d="M5 0a5 5 0 0 0-5 5c0 4 5 9 5 9s5-5 5-9a5 5 0 0 0-5-5zm0 7a2 2 0 1 1 0-4 2 2 0 0 1 0 4z" fill="#fff"/></svg>
    218 Larkspur Avenue Tampa, USA 33602
  </div>
  <div class="abs tel">
    <svg width="13" height="13" viewBox="0 0 24 24"><path d="M6.6 10.8a15 15 0 0 0 6.6 6.6l2.2-2.2c.3-.3.7-.4 1-.2 1.1.4 2.3.6 3.6.6.6 0 1 .4 1 1V20c0 .6-.4 1-1 1A17 17 0 0 1 3 4c0-.6.4-1 1-1h3.5c.6 0 1 .4 1 1 0 1.3.2 2.5.6 3.6.1.3 0 .7-.2 1z" fill="#fff"/></svg>
    Tel: <b>555-014-2290</b>
  </div>
</div>

<header class="abs header">
  <div class="abs brand"><span class="dot"></span>Solvane Wellness USA</div>
  <nav class="abs nav">
    <a class="active" href="#">HOME</a>
    <a href="#">ABOUT US</a>
    <a href="#">TREATMENT</a>
    <a href="#">FAQ</a>
    <a href="#">CONTACT US</a>
  </nav>
</header>

<section class="abs hero" role="img" aria-label="Photo of a young woman resting her head in her hand, looking weary">
  <div class="abs brand"><span class="dot"></span>Solvane Wellness USA</div>
</section>

<div class="abs card c1">
  <h3>DEPRESSION</h3>
  <p>Nemo enim ipsam voluptatem quia voluptas sit aspernatur aut odit aut fugit, sed quias.</p>
  <span class="btn">Read More</span>
</div>
<div class="abs card c2">
  <h3>BIPOLAR</h3>
  <p>Nemo enim ipsam voluptatem quia voluptas sit aspernatur aut odit aut fugit, sed quias.</p>
  <span class="btn">Read More</span>
</div>
<div class="abs card c3">
  <h3>CHRONIC PAIN</h3>
  <p>Nemo enim ipsam voluptatem quia voluptas sit aspernatur aut odit aut fugit, sed quias.</p>
  <span class="btn">Read More</span>
</div>

<section class="abs schedule">
  <h2 class="abs">SCHEDULE YOUR APPOINTMENT ONLINE</h2>
  <div class="abs book">BOOK AN APPOINTMENT</div>
</section>

<h2 class="abs sec-title" style="top:942px">SOLVANE WELLNESS</h2>

<div class="abs feature" style="left:108px">
  <div class="icon" role="img" aria-label="Icon of a head with a thought symbol"><span></span></div>
  <h3>BIPOLAR</h3>
  <p>Nemo enim ipsam voluptatem quia voluptas sit aspernatur aut odit aut fugit, sed quis.</p>
  <span class="more">Read More &gt;&gt;</span>
</div>
<div class="abs feature" style="left:459px">
  <div class="icon" role="img" aria-label="Icon of a person hugging their knees"><span></span></div>
  <h3>PTSD</h3>
  <p>Nemo enim ipsam voluptatem quia voluptas sit aspernatur aut odit aut fugit, sed quis.</p>
  <span class="more">Read More &gt;&gt;</span>
</div>
<div class="abs feature" style="left:810px">
  <div class="icon" role="img" aria-label="Icon of a person with a headache"><span></span></div>
  <h3>TREATMENT</h3>
  <p>Nemo enim ipsam voluptatem quia voluptas sit aspernatur aut odit aut fugit, sed quis.</p>
  <span class="more">Read More &gt;&gt;</span>
</div>

<section class="abs options">
  <h2 class="abs sec-title" style="top:62px">TREATMENT OPTIONS</h2>
  <div class="abs tile photo1" role="img" aria-label="Photo of a young woman holding her temple, eyes closed"></div>
  <div class="abs tile text t1">
    <h3>NEMO ENIM IPSAM</h3>
    <p>Sed ut perspiciatis unde omnis iste natus error sit voluptatem accusantium libero tempore, cum soluta nobis est eligendi optio cumque.</p>
    <span class="btn">Read More</span>
  </div>
  <div class="abs tile photo2" role="img" aria-label="Photo of a teenage girl talking during a counselling session"></div>
  <div class="abs tile text t2">
    <h3>NEMO ENIM IPSAM</h3>
    <p>Sed ut perspiciatis unde omnis iste natus error sit voluptatem accusantium libero tempore, cum soluta nobis est eligendi optio cumque.</p>
    <span class="btn">Read More</span>
  </div>
</section>

<h2 class="abs sec-title" style="top:2020px">SIGN UP FOR OUR NEWSLETTER</h2>
<p class="abs news-p">I'm a paragraph. Click here to add your own text and edit me. Let your users get to know you.</p>
<div class="abs email">Enter Your Email Here</div>
<div class="abs subscribe">Subscribe Now</div>

<footer class="abs footer">
  <div class="abs brand"><span class="dot"></span>Solvane Wellness USA</div>
  <span class="abs social" style="left:995px" aria-label="Social link"></span>
  <span class="abs social" style="left:1046px" aria-label="Social link"></span>
  <div class="abs rule"></div>
  <div class="abs copy">Copyrights @ 2019 Solvane Wellness. All Rights Reserved.</div>
</footer>

</body>
</html>
```